Financial investment calculator report for real estae - layout & design

I am looking to Create a web report utilizing the attached information. It is an investment calculator report that will be customized report based on an online calculator. Therefore the report will need to be designed in a manner that a backend developer will be able to build off of.

The report will need to be web based but also printed in PDF format. The report will need to include the calculation format as well as be templeted to add a report user unique profile information like Headshot, Business Logo, Name, Telephone number, email etc.

The report should be modern and clean and easy to read and use a modern clean template design. It should be able to be easily color customized by the end user to produce templets in Red, Blue, Green, and Greyscale.

The report should be no more than 3 pages total with out breaking up the sections.

Section One - Cover sheet including agent bio info, Report Title and property address (both prominent), 400 Character space for property description, Property Pictures (3), and a google Maps integration image showing property location, It should also have room for about 100 words for a text disclaimer. (I will provide text soon)

Section Two - Inputs from the calculator

Section 3 - The Four Benefits & Rates of Return

Once I have a completed/approved form I will have about a half dozen forms/reports that will need to be laid out with a similar aesthetic.

Feel free to ask me any questions. Thank You
Milo

Target Market(s)

This report will be produced by real estate agents forvtheir investor clients. It should denote professionalism

Font styles to use
Sans Serif

Colors
0054AA
0677BA
7BADD7
CADEEF
E8F1F8
00AB8E
00BBA5
67D7C9
C6EFE9
E9F9F6
EB3D1F
EC4F4E
F09395
F8D3D4
FCEDEE

```html
<!DOCTYPE html>
<html lang="en">
<head>
<meta charset="utf-8">
<title>Investment Analysis – 418 Larkfield</title>
<link href="https://fonts.googleapis.com/css2?family=Lato:wght@300;400;700&display=swap" rel="stylesheet">
<style>
:root{
  --accent:#2410e8;
  --ink:#111;
  --text:#3a3a3a;
  --muted:#666;
  --rule:#e2e2e2;
  --band:#efefef;
  --card:#fbfbfb;
  --neg:#ef5350;
  --page:#fff;
}
*{box-sizing:border-box;margin:0;padding:0}
html,body{width:849px;height:1200px;overflow:hidden;background:var(--page)}
body{font-family:'Lato',Arial,sans-serif;color:var(--ink);position:relative}
.abs{position:absolute}
.agency-mark{left:45px;top:15px;width:70px;height:70px;border-radius:50%;background:#000}
.agency-name{left:136px;top:41px;font-size:15px;font-weight:700;letter-spacing:.2px}
.agency-name span{font-weight:300}
.agent{right:201px;top:28px;text-align:right}
.agent-name{font-size:16px;color:var(--accent);font-weight:400;letter-spacing:.3px}
.agent-name b{font-weight:700}
.agent-line{font-size:11px;margin-top:6px;display:flex;justify-content:flex-end;align-items:center;gap:14px}
.headshot{left:682px;top:30px;width:113px;height:122px;border-radius:8px;background:linear-gradient(160deg,#5a8f9a 0%,#2f4a3c 55%,#1f3326 100%);box-shadow:0 2px 6px rgba(0,0,0,.2)}
.rule-grey{left:38px;top:114px;width:774px;height:1px;background:var(--rule)}
.rule-accent{left:38px;top:113px;width:273px;height:2px;background:var(--accent)}
.page-title{left:37px;top:121px;font-size:29px;font-weight:700;letter-spacing:-.2px}
.page-title span{font-weight:300}
.map{left:39px;top:183px;width:344px;height:189px;border-radius:8px;background:linear-gradient(90deg,#9fbff4 0%,#e9ecee 18%,#eceeee 70%,#9cbff6 86%);box-shadow:0 2px 6px rgba(0,0,0,.15)}
.prop-title{left:414px;top:176px;font-size:24px;font-weight:700}
.prop-sub{left:414px;top:206px;font-size:10.5px;font-weight:700}
.prop-desc{left:416px;top:229px;width:390px;font-size:8.1px;line-height:13.5px;color:var(--muted)}
.prop-addr{left:414px;top:323px;font-size:10.5px;display:flex;align-items:center;gap:5px}
.price-label{left:416px;top:349px;font-size:11.5px;font-weight:700}
.price-value{right:63px;top:345px;font-size:15px;font-weight:700;color:var(--accent)}
.card{left:39px;top:401px;width:773px;height:754px;border-radius:8px;background:var(--card);box-shadow:0 1px 6px rgba(0,0,0,.12)}
.band{left:54px;width:736px;height:29px;border-radius:5px;background:var(--band);display:flex;align-items:center;font-size:11.5px;font-weight:700}
.band::before{content:"";width:4px;height:4px;border-radius:50%;background:var(--accent);margin:0 14px 0 14px}
.band .band-title{width:324px}
.band .col{font-size:8.2px;font-weight:400}
.band .right{margin-left:auto;margin-right:13px;font-size:8.2px;font-weight:400}
.rows{left:96px;width:694px}
.row{display:grid;grid-template-columns:177px 144px 198px 175px;height:20.4px;align-items:center;border-bottom:1px solid var(--rule);font-size:8.2px;color:var(--text)}
.row > :last-child{text-align:right}
.neg{color:var(--neg)}
.sub-head{left:96px;top:1020px;font-size:12px;font-weight:700}
.line{height:2px;background:var(--accent)}
.summary{font-size:11.5px;font-weight:700}
.summary-val{font-size:11.5px;font-weight:700;text-align:right}
.footer{left:38px;top:1178px;font-size:8px;color:var(--muted)}
.page-num{right:37px;top:1178px;font-size:8px;color:var(--muted)}
</style>
</head>
<body>
<div class="abs agency-mark"></div>
<div class="abs agency-name">AGENCYNAME <span>HERE</span></div>

<div class="abs agent">
  <div class="agent-name"><b>SALEMANS</b> NAME</div>
  <div class="agent-line">
    <svg width="10" height="10" viewBox="0 0 24 24" fill="none" stroke="#111" stroke-width="2"><path d="M5 3h4l2 5-3 2a11 11 0 0 0 6 6l2-3 5 2v4a2 2 0 0 1-2 2A18 18 0 0 1 3 5a2 2 0 0 1 2-2z"/></svg>
    <span>(555) 014-2287</span>
  </div>
  <div class="agent-line">agent@harborkey.com</div>
</div>
<div class="abs headshot" role="img" aria-label="Agent headshot photo"></div>

<div class="abs rule-grey"></div>
<div class="abs rule-accent"></div>
<h1 class="abs page-title">Investment <span>Analysis:</span></h1>

<div class="abs map" role="img" aria-label="Map showing the property location"></div>

<div class="abs prop-title">418 LARKFIELD</div>
<div class="abs prop-sub">15-Plex of 1bd/1bth Apartments</div>
<p class="abs prop-desc">Urban bliss in this chic 400 sqft apartment. Step into a bright and open space with stylish décor. Relax on a cozy sofa or entertain in the dining area. The well-equipped kitchen features modern appliances and ample storage. Unwind in the tranquil bedroom with a queen-sized bed. Refresh in the pristine bathroom with a walk-in shower. Enjoy high-speed internet, a smart TV, and laundry facilities. Take in city views from the private balcony. Explore trendy cafes, shops, and restaurants nearby. Embrace the perfect blend of comfort and style in this urban sanctuary.</p>
<div class="abs prop-addr">
  <svg width="8" height="11" viewBox="0 0 16 22"><path d="M8 0a8 8 0 0 0-8 8c0 6 8 14 8 14s8-8 8-14a8 8 0 0 0-8-8zm0 11a3 3 0 1 1 0-6 3 3 0 0 1 0 6z" fill="#111"/></svg>
  418 Larkfield Ave, Riverton, KS 66210
</div>
<div class="abs price-label">PURCHASE PRICE:</div>
<div class="abs price-value">$1.690.000</div>

<div class="abs card"></div>

<div class="abs band" style="top:411px"><span class="band-title">PROPERTY ADDRESS:</span><span class="right">418 Larkfield Ave, Riverton, KS 66210</span></div>
<div class="abs rows" style="top:441px">
  <div class="row"><span>Financing</span><span></span><span>20% Down</span><span>20 Year Conventional</span></div>
  <div class="row"><span>Purchase Price</span><span></span><span></span><span>$1.690.000</span></div>
  <div class="row"><span>Down Payment (Cash Invested)</span><span></span><span>20% of purchase price</span><span>$338.000</span></div>
  <div class="row"><span>Amount Financed</span><span></span><span></span><span>$1.352.000</span></div>
  <div class="row"><span>Needed Capital Improvements Est</span><span></span><span></span><span>$0</span></div>
  <div class="row"><span>Est. Closing Costs</span><span></span><span></span><span>$3.000</span></div>
  <div class="row"><span>CASH Invested (Down Pmt. + Closing Costs)</span><span></span><span></span><span>$341.000</span></div>
</div>
<div class="abs line" style="left:96px;top:582px;width:694px"></div>
<div class="abs rows" style="top:588px">
  <div class="row" style="border:0"><span class="summary">Rate: 7%</span><span class="summary">Term: 20 years</span><span class="summary">Monthly P&amp;I:</span><span class="summary-val">$10.482</span></div>
</div>

<div class="abs band" style="top:613px"><span class="band-title">DEPRICIATION (FIRST YEAR): (ASSUMES 80%/20%)</span><span class="col" style="width:198px">Est. Value</span><span class="col">Yearly Rate</span></div>
<div class="abs rows" style="top:642px">
  <div class="row"><span>Land Cost</span><span>0 Year</span><span>$338.000</span><span style="display:flex;justify-content:space-between"><span>0%</span><span>$0</span></span></div>
  <div class="row"><span>Personal Property Cost</span><span>5 Years</span><span>$45.000</span><span style="display:flex;justify-content:space-between"><span>20%</span><span>$9.000</span></span></div>
  <div class="row"><span>Building Cost</span><span>27.5 Years</span><span>$1.262.000</span><span style="display:flex;justify-content:space-between"><span>3.48%</span><span>$43.918</span></span></div>
  <div class="row"><span>Land Improvement Cost</span><span>15 Years</span><span>$45.000</span><span style="display:flex;justify-content:space-between"><span>5%</span><span>$2.250</span></span></div>
</div>
<div class="abs line" style="left:417px;top:723px;width:373px"></div>
<div class="abs summary" style="left:417px;top:729px">Total Depreciation:</div>
<div class="abs summary-val" style="right:59px;top:727px">$55.168</div>

<div class="abs band" style="top:753px"><span class="band-title">INCOME:</span></div>
<div class="abs rows" style="top:783px">
  <div class="row"><span>Annual Rent</span><span></span><span></span><span>$170.000</span></div>
  <div class="row"><span>Other Income</span><span></span><span></span><span>$0</span></div>
  <div class="row"><span>Less Vacancy</span><span></span><span>est. 5% of annual rent</span><span class="neg">-$0</span></div>
</div>
<div class="abs line" style="left:417px;top:843px;width:373px"></div>
<div class="abs summary" style="left:417px;top:850px">Gross Operating Income:</div>
<div class="abs summary-val" style="right:59px;top:850px">$170.000</div>

<div class="abs band" style="top:875px"><span class="band-title">EXPENSES:</span></div>
<div class="abs rows" style="top:905px">
  <div class="row"><span>Real Estate Tax</span><span></span><span></span><span>$27.439</span></div>
  <div class="row"><span>Insurance</span><span></span><span>est.</span><span>$3.492</span></div>
  <div class="row"><span>Association Dues/HOA's</span><span></span><span></span><span>$0</span></div>
  <div class="row"><span>Management</span><span></span><span>0%</span><span>$0</span></div>
  <div class="row"><span>Utilities</span><span></span><span></span><span>$9.192</span></div>
</div>
<div class="abs sub-head">PROPERTY ADDRESS</div>
<div class="abs rows" style="top:1036px">
  <div class="row"><span>Advertising</span><span></span><span></span><span>$170.000</span></div>
  <div class="row"><span>Maintnence</span><span></span><span>est.</span><span>$40.123</span></div>
  <div class="row"><span>Miscellaneous1</span><span></span><span>est.</span><span>$129.877</span></div>
  <div class="row"><span>Miscellaneous2</span><span></span><span>est.</span><span>$125.784</span></div>
</div>
<div class="abs line" style="left:417px;top:1117px;width:373px"></div>
<div class="abs summary" style="left:417px;top:1123px">Total Expenses:</div>
<div class="abs summary-val" style="right:59px;top:1122px">$4.092</div>

<div class="abs footer">418 Larkfield, REF #47v8487 by Northgate Realty | Report at www.harborkey-reports.com. June 26th, 2023</div>
<div class="abs page-num">Page 2/3</div>
</body>
</html>
```